Business cards and stationary design

We just completed the design of our new logo and we need to print new business cards and letterhead for our nonprofit. We are looking for a fresh new design that shows off our new logo. On letterhead, we must have a column on the right or left to include our Board of Directors (up to 45 names) (see attachment)

Industry/Entity Type

Non-Profit

Contact Information for Business Card

Standard business card with name, title, Company name, mailing address phone numbers, email address and website. Tagline on back "Bringing the homeless home"

Font styles to use
Sans Serif

Requirements
Must have
• include pertinent information above
• new logo
• fonts compatible with logo
• should use logo colors only
Nice to have
• tag lines

```html
<!DOCTYPE html>
<html lang="en">
<head>
<meta charset="utf-8">
<title>Shelter Bridge Center – Business Card</title>
<link href="https://fonts.googleapis.com/css2?family=Bebas+Neue&family=Work+Sans:wght@400;500;600&display=swap" rel="stylesheet">
<style>
  :root {
    --backdrop: #1c1c1d;
    --card: #222223;
    --card-edge: #2c2c2d;
    --gold: #f7b51e;
    --teal: #1592b4;
    --text: #f1f1f1;
  }
  * { margin: 0; padding: 0; box-sizing: border-box; }
  html, body { width: 1200px; height: 900px; overflow: hidden; background: var(--backdrop); }
  .canvas {
    width: 1200px; height: 900px;
    display: flex; flex-direction: column; align-items: center; justify-content: center;
    gap: 24px;
  }
  .card {
    position: relative;
    width: 700px; height: 400px;
    background: linear-gradient(135deg, var(--card) 0%, var(--card-edge) 100%);
    border-bottom: 6px solid var(--gold);
    box-shadow: 0 10px 24px rgba(0,0,0,.45);
    font-family: "Work Sans", sans-serif;
    color: var(--text);
  }
  .card--front { display: flex; align-items: center; justify-content: center; }
  .brand { display: flex; align-items: center; gap: 16px; margin-top: -30px; }
  .brand__mark { width: 22px; height: 22px; border-radius: 50%; background: var(--teal); }
  .brand__name {
    font-family: "Work Sans", sans-serif; font-weight: 600;
    font-size: 34px; letter-spacing: 5px; text-transform: uppercase;
    color: var(--teal);
  }
  .card--back .identity {
    position: absolute; left: 150px; top: 150px; width: 260px; text-align: right;
  }
  .identity__name {
    font-family: "Bebas Neue", sans-serif; font-size: 46px; line-height: 1;
    color: var(--gold); letter-spacing: .5px;
  }
  .identity__title { font-size: 17px; margin-top: 4px; }
  .divider {
    position: absolute; left: 440px; top: 150px; width: 3px; height: 60px; background: var(--gold);
  }
  .contacts {
    position: absolute; left: 470px; top: 146px; list-style: none;
    font-size: 17px; line-height: 24px; letter-spacing: .4px;
  }
  .contacts li { display: flex; align-items: center; gap: 10px; }
  .contacts svg { width: 12px; height: 12px; flex: none; }
  .address {
    position: absolute; left: 0; right: 0; bottom: 60px; text-align: center;
    font-size: 18px; letter-spacing: .6px;
  }
</style>
</head>
<body>
<main class="canvas">
  <section class="card card--front">
    <div class="brand">
      <span class="brand__mark"></span>
      <span class="brand__name">Shelter Bridge Center</span>
    </div>
  </section>

  <section class="card card--back">
    <div class="identity">
      <h1 class="identity__name">Daniel Reyes</h1>
      <p class="identity__title">Director</p>
    </div>
    <span class="divider"></span>
    <ul class="contacts">
      <li>
        <svg viewBox="0 0 12 12" aria-hidden="true"><path d="M2.5 1 L4.5 1 L5.2 3.4 L4 4.4 Q5 6.8 7.6 8 L8.6 6.8 L11 7.5 L11 9.5 Q10.5 11 9 11 Q1 10 1 3 Q1 1.5 2.5 1Z" fill="var(--gold)"/></svg>
        555.014.2290
      </li>
      <li>
        <svg viewBox="0 0 12 12" aria-hidden="true"><rect x="1" y="2.5" width="10" height="7" fill="none" stroke="var(--gold)" stroke-width="1.2"/><path d="M1 2.5 L6 6.5 L11 2.5" fill="none" stroke="var(--gold)" stroke-width="1.2"/></svg>
        info@sbcfairview.org
      </li>
      <li>
        <svg viewBox="0 0 12 12" aria-hidden="true"><circle cx="6" cy="6" r="5" fill="none" stroke="var(--gold)" stroke-width="1.1"/><ellipse cx="6" cy="6" rx="2.2" ry="5" fill="none" stroke="var(--gold)" stroke-width="1"/><path d="M1 6 H11" stroke="var(--gold)" stroke-width="1"/></svg>
        www.sbcfairview.org
      </li>
    </ul>
    <p class="address">P.O. Box 50218, Fairview, Texas 75069</p>
  </section>
</main>
</body>
</html>
```